Custom Cabinet Shop Needs a website design

Hi,
We need a website for a Custom Cabinet Shop and Cabinet parts manufacturing business.
The business has two sides to it. One side provides custom Kitchens, vanities, entertainment units, offices and what not to homeowners and contractors.
The 2nd side of the business provides built to order cabinet boxes and other parts required to put together a project to other cabinet shops, small contractors looking to install there own cabinets.
Website will need a Gallery to display work.
Color scheme to go well with logo.
current website is www.brambleoakcustomcabinets.com
being changed to www.brambleoak.ca
Logo Included in attached files.
Tagline "Joinery with Spirit"
Mission Statement "Our passion is to deliver inspired cabinetry solutions to suit all your needs, supported by our phenomenal star class customer service"
The website should convey quality and professionalism.
Thank you.
Homeowners/ Contractors
Entertainment

```html
<!DOCTYPE html>
<html lang="en">
<head>
<meta charset="utf-8">
<title>Bramble Oak Custom Cabinets</title>
<link rel="stylesheet" href="https://fonts.googleapis.com/css2?family=Lato:wght@400;700&family=PT+Sans+Narrow&display=swap">
<style>
:root{
  --orange:#f05a24;
  --ink:#333333;
  --text:#555555;
  --grey-card:#5e5e5e;
  --hero-bg:#f1f1f1;
  --footer:#151515;
  --footer-base:#0b0b0b;
  --footer-text:#a8a8a8;
  --line:#7a7a7a;
}
*{box-sizing:border-box;margin:0;padding:0}
html,body{width:935px;height:1200px;overflow:hidden;background:#fff}
body{font-family:"Lato",sans-serif;color:var(--text);position:relative}
.abs{position:absolute}
.top-rule{top:0;left:0;width:935px;height:3px;background:#b9b9b9}

/* header */
.brand{left:87px;top:40px;font-size:22px;font-weight:700;color:var(--ink);display:flex;align-items:center;gap:8px;letter-spacing:.5px}
.brand-mark{width:18px;height:18px;background:var(--orange)}
.social{top:22px;left:718px;display:flex;gap:8px}
.social span{width:25px;height:25px;border-radius:50%;background:var(--orange)}
.nav{top:60px;right:87px;display:flex;align-items:center;font-size:11.5px;color:var(--ink);letter-spacing:.3px}
.nav a{color:inherit;text-decoration:none;padding:6px 9px}
.nav a.active{background:#444;color:#fff}
.nav .sep{padding:0 9px;font-size:10px}

/* hero */
.hero{top:109px;left:0;width:935px;height:357px;background:var(--hero-bg)}
.hero-photo{top:109px;left:340px;width:595px;height:330px;background:linear-gradient(90deg,rgba(241,241,241,1) 0%,rgba(206,199,192,.9) 18%,#b7aca2 45%,#3a2a24 60%,#4a3a33 80%,#d8d2cc 100%)}
.hero-title{left:86px;top:188px;font-family:"PT Sans Narrow",sans-serif;font-size:30px;color:#444;letter-spacing:.5px}
.hero-title b{color:var(--orange);font-weight:700}
.hero-copy{left:86px;top:229px;width:320px;font-size:11.6px;line-height:18.7px;color:#444}
.btn{left:86px;top:312px;width:120px;height:33px;background:var(--orange);color:#fff;font-size:11.5px;font-weight:700;display:flex;align-items:center;justify-content:center;letter-spacing:.3px}
.dots{left:89px;top:366px;display:flex;gap:6px}
.dots span{width:22px;height:3px;background:#b8c6c8}
.dots span:first-child{background:#444}

/* service cards */
.cards{top:439px;left:84px;width:766px;height:280px;background:#fff;box-shadow:0 0 4px rgba(0,0,0,.12)}
.card{top:450px;width:177px;height:252px;color:#fff;text-align:center}
.card .photo{height:107px;background:linear-gradient(180deg,#c9c4bd,#6b5a4e)}
.card.grey{background:var(--grey-card)}
.card.orange{background:var(--orange)}
.card .badge{position:absolute;left:66px;top:90px;width:44px;height:44px;border-radius:50%;border:3px solid #fff;background:inherit}
.card.grey .badge{background:var(--grey-card)}
.card.orange .badge{background:var(--orange)}
.card h3{margin-top:35px;font-size:18px;font-weight:400}
.card p{margin:6px 12px 0;font-size:11px;line-height:15.6px}

/* sections */
.sec-head{font-size:16.5px;font-weight:700;color:var(--ink);padding-left:20px;padding-bottom:6px;border-bottom:2px solid var(--line)}
.sec-head b{color:var(--orange)}
.sec-head::before{content:"";position:absolute;left:4px;top:-2px;width:2px;height:26px;background:var(--orange);transform:skewX(-22deg)}
.who{left:97px;top:746px;width:456px}
.who p{margin-top:17px;padding-left:4px;font-size:11.7px;line-height:18.7px;color:#555}
.news{left:579px;top:746px;width:256px}
.news-item{display:flex;gap:12px;margin-top:17px}
.date{width:43px;flex:none}
.date .d{height:26px;background:var(--orange);color:#fff;font-size:17px;text-align:center;line-height:26px}
.date .m{height:23px;background:#555;color:#fff;font-size:9.5px;text-align:center;line-height:23px}
.news-item h4{font-size:13.5px;font-weight:400;color:#333}
.news-item p{font-size:10.8px;line-height:16.4px;margin-top:3px;color:#555}

/* footer */
.footer{top:944px;left:0;width:935px;height:209px;background:var(--footer)}
.fcol{top:972px;color:var(--footer-text);font-size:10.8px}
.fcol h5{font-size:13px;font-weight:400;color:#fff;padding-bottom:9px;border-bottom:1px solid #555;margin-bottom:12px}
.fcol li{list-style:none;height:20.3px}
.fcol li::before{content:"›";margin:0 8px 0 2px}
.contact-row{display:flex;gap:10px;margin-bottom:4px;line-height:17px}
.contact-row svg{flex:none;margin-top:2px}
.phone{font-size:14px;color:#ccc}
.foot-brand{left:655px;top:1040px;font-size:18px;font-weight:700;color:#fff;display:flex;align-items:center;gap:8px}
.foot-brand span{width:15px;height:15px;background:var(--orange)}
.base{top:1153px;left:0;width:935px;height:47px;background:var(--footer-base);color:#b8b8b8;font-size:11px}
.base .copy{position:absolute;left:96px;top:17px}
.base .legal{position:absolute;right:107px;top:17px}
.base .legal i{font-style:normal;margin:0 11px}
</style>
</head>
<body>
<div class="abs top-rule"></div>

<header>
  <div class="abs brand"><span class="brand-mark"></span>BRAMBLE OAK</div>
  <div class="abs social" aria-label="Social links"><span></span><span></span><span></span><span></span></div>
  <nav class="abs nav">
    <a class="active">HOME</a><span class="sep">I</span>
    <a>GALLERY</a><span class="sep">I</span>
    <a>SERVICES</a><span class="sep">I</span>
    <a>WARRANTY</a><span class="sep">I</span>
    <a>CONTACT</a>
  </nav>
</header>

<section>
  <div class="abs hero"></div>
  <div class="abs hero-photo" role="img" aria-label="Photo of a dark wood entertainment unit with shelves and drawers"></div>
  <h1 class="abs hero-title" style="font-weight:400">JOINERY WITH <b>SPIRIT</b></h1>
  <p class="abs hero-copy">Lorem Ipsum is simply dummy text of the printing and type-setting industry. Lorem Ipsum has been the industry's stand-ard dummy text ever since the 1500s release of Letraset sheets containing Lorem Ipsum passages.</p>
  <div class="abs btn">LEARN MORE</div>
  <div class="abs dots"><span></span><span></span><span></span><span></span></div>
</section>

<section>
  <div class="abs cards"></div>
  <div class="abs card grey" style="left:96px"><div class="photo" role="img" aria-label="Photo of a residential kitchen"></div><span class="badge"></span><h3>Residential</h3><p>Lorem Ipsum is simply dummy text of the printing and typeset-ting industry. Lorem Ipsum has been the industry's has been.</p></div>
  <div class="abs card orange" style="left:284px"><div class="photo" role="img" aria-label="Photo of a kitchen with pendant lights"></div><span class="badge"></span><h3>Business</h3><p>Lorem Ipsum is simply dummy text of the printing and typeset-ting industry. Lorem Ipsum has been the industry's has been.</p></div>
  <div class="abs card grey" style="left:472px"><div class="photo" role="img" aria-label="Photo of a dining nook by large windows"></div><span class="badge"></span><h3>Gallery</h3><p>Lorem Ipsum is simply dummy text of the printing and typeset-ting industry. Lorem Ipsum has been the industry's has been.</p></div>
  <div class="abs card orange" style="left:661px"><div class="photo" role="img" aria-label="Photo of a kitchen with island seating"></div><span class="badge"></span><h3>Warranty</h3><p>Lorem Ipsum is simply dummy text of the printing and typeset-ting industry. Lorem Ipsum has been the industry's has been.</p></div>
</section>

<section class="abs who">
  <h2 class="sec-head"><b>WHO</b> WE ARE</h2>
  <p>Lorem Ipsum is simply dummy text of the printing and typesetting industry. Lorem Ipsum has been the industry's standard dummy text ever since the 1500s, when an unknown printer took a galley of type and scrambled it to make a type specimen book. It has sur-vived not only five centuries, but also the leap into electronic typesetting, remaining essentially unchanged. It was popularised in the 1960s with the release of Letraset sheets containing Lorem Ipsum passages, and more recently with desktop publishing software like Aldus PageMaker including versions of Lorem Ipsum.</p>
</section>

<section class="abs news">
  <h2 class="sec-head"><b>LATEST</b> NEWS</h2>
  <div class="news-item"><div class="date"><div class="d">01</div><div class="m">MAR</div></div><div><h4>Lorem Ipsum is simply</h4><p>Lorem Ipsum is simply dummy text of the printing and typesetting industry.</p></div></div>
  <div class="news-item"><div class="date"><div class="d">01</div><div class="m">MAR</div></div><div><h4>Lorem Ipsum is simply</h4><p>Lorem Ipsum is simply dummy text of the printing and typesetting industry.</p></div></div>
</section>

<footer>
  <div class="abs footer"></div>
  <div class="abs fcol" style="left:99px;width:139px"><h5>Who We Are</h5><ul><li>Home</li><li>Gallery</li><li>Services</li><li>Warranty</li><li>Contact</li></ul></div>
  <div class="abs fcol" style="left:252px;width:170px"><h5>Our Services</h5><ul><li>Lorem Ipsum Dolor Sit Amet</li><li>Typesetting Industry</li><li>Have been Sent in Lorem</li><li>Services Which Done</li><li>Inside Vehicula Quis</li></ul></div>
  <div class="abs fcol" style="left:453px;width:170px"><h5>Contact Us</h5>
    <div class="contact-row"><svg width="12" height="14" viewBox="0 0 12 14"><path d="M6 0a5 5 0 0 0-5 5c0 4 5 9 5 9s5-5 5-9a5 5 0 0 0-5-5zm0 7a2 2 0 1 1 0-4 2 2 0 0 1 0 4z" fill="#888"/></svg><div>4820 Range Road 190<br>Rocky View, Alberta<br>T1X 2K4</div></div>
    <div class="contact-row phone"><svg width="12" height="14" viewBox="0 0 12 14"><path d="M2 0l3 3-1.5 2a8 8 0 0 0 4 4L9 7.5l3 3L10 13C5 13 0 8 0 3z" fill="#888"/></svg><div>403-555-0178</div></div>
    <div class="contact-row" style="margin-top:6px;white-space:nowrap"><svg width="15" height="11" viewBox="0 0 15 11"><rect width="15" height="11" fill="#888"/><path d="M0 0l7.5 6L15 0" stroke="#151515" fill="none"/></svg><div>sales@brambleoakcustomcabinets.com</div></div>
  </div>
  <div class="abs foot-brand"><span></span>BRAMBLE OAK</div>
  <div class="abs base">
    <div class="copy">copyright©2015.Bramble Oak Cabinet. All Rights Reserved</div>
    <div class="legal">Privacy Policy<i>I</i>Terms &amp; Conditions</div>
  </div>
</footer>
</body>
</html>
```